Brookvane Consulting Business Card Design

Business Card Design for Brookvane Consulting. Brookvane Consulting is a boutique consultancy based in Atlanta, GA., that specializes in marketing strategy, organization planning, and leadership development. We provide solutions for small businesses and startups as well as Vantage 300 companies.

http://brookvaneconsulting.com/

Target Market(s)

We provide solutions for small businesses and startups as well as Vantage 300 companies.

Industry/Entity Type

Consulting

Contact Information for Business Card

Two sided business card with priority on contact information, logo, tag line (Inspiration to Dream More, Do More, Become More)

Colors

Designer to choose colors to be used in the design.

Requirements
Must have
• contact information, logo, tag line (Inspiration to Dream More, Do More, Become More)
• Simple no over communication.
Nice to have
• I would like to see different placements of logo and creative use of both sides of the card
Should not have
• Do not put too much information on the card.

```html
<!DOCTYPE html>
<html lang="en">
<head>
<meta charset="utf-8">
<title>Brookvane Consulting Business Card</title>
<link rel="stylesheet" href="https://fonts.googleapis.com/css2?family=Lato:wght@400;700&family=Tinos:ital@1&display=swap">
<style>
  :root {
    --backdrop: #545454;
    --card-white: #ffffff;
    --card-black: #0b0b0b;
    --ink: #2a2a2a;
    --ink-soft: #3c3c3c;
    --rule: #9a9aa2;
    --paper-text: #ffffff;
    --pattern-light: #3a3a3a;
    --pattern-dark: #0e0e0e;
  }
  html, body {
    margin: 0;
    width: 1200px;
    height: 900px;
    overflow: hidden;
    background: var(--backdrop);
    font-family: "Lato", sans-serif;
  }
  .stage { position: relative; width: 1200px; height: 900px; }
  .card {
    position: absolute;
    top: 170px;
    width: 347px;
    height: 560px;
    overflow: hidden;
  }
  .card--front { left: 259px; background: var(--card-white); color: var(--ink); }
  .card--back { left: 631px; background: var(--card-black); color: var(--paper-text); }

  .wordmark {
    position: absolute;
    left: 0; right: 0;
    text-align: center;
    font-weight: 700;
    font-size: 34px;
    line-height: 1.1;
    letter-spacing: 0.5px;
    margin: 0;
  }
  .card--front .wordmark { top: 128px; color: var(--ink); }
  .card--back .wordmark { top: 382px; color: var(--paper-text); }

  .contact {
    position: absolute;
    top: 330px; left: 0; right: 0;
    text-align: center;
  }
  .contact__name { font-size: 21px; font-weight: 700; letter-spacing: 0.5px; margin: 0; color: var(--ink); }
  .contact__role { font-size: 14px; margin: 2px 0 0; color: var(--ink-soft); }
  .contact__rule { width: 143px; height: 1px; background: var(--rule); margin: 10px auto 12px; border: 0; }
  .contact__line { font-size: 14px; margin: 0 0 4px; color: var(--ink); }
  .contact__line b { font-weight: 700; }
  .contact__web { font-weight: 700; }

  .tagline-band {
    position: absolute;
    left: 0; right: 0; bottom: 0;
    height: 83px;
    background: var(--card-black);
    color: var(--paper-text);
    display: flex;
    align-items: center;
    justify-content: center;
  }
  .tagline {
    margin: 0;
    font-family: "Tinos", serif;
    font-style: italic;
    font-size: 23px;
    line-height: 30px;
    text-align: center;
  }

  .pattern-field {
    position: absolute;
    left: 0; right: 0; top: 0;
    height: 380px;
    background: linear-gradient(160deg, var(--pattern-light) 0%, #1c1c1c 55%, var(--pattern-dark) 100%);
  }
  .back-web {
    position: absolute;
    top: 514px; left: 0; right: 0;
    text-align: center;
    font-size: 16px;
    letter-spacing: 1.6px;
    margin: 0;
  }
</style>
</head>
<body>
<main class="stage">
  <section class="card card--front">
    <p class="wordmark">Brookvane<br>Consulting</p>
    <div class="contact">
      <p class="contact__name">DANIEL REYES</p>
      <p class="contact__role">Managing Director</p>
      <hr class="contact__rule">
      <p class="contact__line"><b>P:</b> 555-014-2290</p>
      <p class="contact__line"><b>E:</b> hello@brookvanemail.com</p>
      <p class="contact__line contact__web">www.brookvaneconsulting.com</p>
    </div>
    <div class="tagline-band">
      <p class="tagline">Inspiration to Dream More,<br>Do More, Become More</p>
    </div>
  </section>

  <section class="card card--back">
    <div class="pattern-field" role="img" aria-label="Repeating pattern of the brand symbol in dark grey tones"></div>
    <p class="wordmark">Brookvane<br>Consulting</p>
    <p class="back-web">www.brookvaneconsulting.com</p>
  </section>
</main>
</body>
</html>
```